BUSINESS CARD DESIGN

NAME- DALE VORSKIN
PHONE NUMER - 555- 714-9082
EMAIL- OFFICE@TRV-GROUNDMAKRZ.COM
BACK OF CARD- SPEACIALIZES IN LAND CLEARING, FORESTRY MUCLHING AND EXCAVATION

Contact Information for Business Card

NAME- DALE VORSKIN PHONE NUMER - 555- 714-9082 EMAIL- OFFICE@TRV-GROUNDMAKRZ.COM BACK OF CARD- SPEACIALIZES IN LAND CLEARING , MUCLHING AND EXCAVATION

```html
<!DOCTYPE html>
<html lang="en">
<head>
<meta charset="utf-8">
<title>Terravale Groundmakrz LLC – Business Card</title>
<link rel="stylesheet" href="https://fonts.googleapis.com/css2?family=Ubuntu:wght@300;500;700&family=Roboto+Condensed:wght@400&display=swap">
<style>
  :root {
    --page-bg: #e4e7e8;
    --brand-yellow: #f5b21a;
    --logo-yellow: #f9c21e;
    --card-dark: #202124;
    --watermark: #2c2a27;
    --text-light: #f4f1ea;
  }
  * { box-sizing: border-box; margin: 0; padding: 0; }
  html, body { width: 1200px; height: 960px; overflow: hidden; }
  body {
    position: relative;
    background: var(--page-bg);
    font-family: "Roboto Condensed", Arial, sans-serif;
  }
  .card {
    position: absolute;
    left: 250px;
    width: 701px;
    height: 400px;
    border-radius: 33px;
    overflow: hidden;
  }
  .card--front { top: 60px; background: var(--brand-yellow); }
  .card--back  { top: 500px; background: var(--card-dark); }

  .brand {
    position: absolute;
    display: flex;
    flex-direction: column;
    align-items: center;
    font-family: "Ubuntu", Arial, sans-serif;
    font-weight: 700;
    text-align: center;
    line-height: 1.15;
    letter-spacing: 2px;
  }
  .brand__dot { border-radius: 50%; margin-bottom: 16px; }
  .card--front .brand { left: 0; right: 0; top: 90px; color: var(--logo-yellow); font-size: 26px; }
  .card--front .brand__dot { width: 120px; height: 120px; background: var(--logo-yellow); }
  .card--back .brand { left: 27px; top: 26px; width: 212px; color: var(--logo-yellow); font-size: 18px; }
  .card--back .brand__dot { width: 110px; height: 110px; background: var(--logo-yellow); margin-bottom: 14px; }

  .tagline {
    position: absolute;
    left: 0; right: 0; top: 356px;
    text-align: center;
    color: var(--text-light);
    font-size: 16.5px;
    letter-spacing: 0.3px;
  }

  .watermark {
    position: absolute;
    left: 661px; top: 61px;
    width: 280px; height: 280px;
    border-radius: 50%;
    background: var(--watermark);
    transform: translateX(-50%);
    margin-left: -140px;
  }

  .name {
    position: absolute;
    right: 26px; top: 176px;
    font-family: "Ubuntu", Arial, sans-serif;
    font-size: 36px;
    color: var(--brand-yellow);
    letter-spacing: 0.5px;
    white-space: nowrap;
  }
  .name__first { font-weight: 700; }
  .name__last { font-weight: 300; }
  .name-bar {
    position: absolute;
    right: 0; top: 180px;
    width: 19px; height: 39px;
    background: var(--brand-yellow);
  }

  .contacts {
    position: absolute;
    left: 32px; top: 304px;
    list-style: none;
    color: var(--text-light);
    font-size: 16.5px;
    letter-spacing: 0.6px;
  }
  .contacts li { display: flex; align-items: center; height: 23px; }
  .contacts svg { width: 16px; height: 16px; margin-right: 10px; fill: var(--brand-yellow); }
</style>
</head>
<body>
  <section class="card card--front">
    <div class="brand">
      <span class="brand__dot"></span>
      <span>TERRAVALE GROUNDMAKRZ</span>
      <span>LLC</span>
    </div>
    <p class="tagline">SPEACIALIZES IN LAND CLEARING , MUCLHING AND EXCAVATION</p>
  </section>

  <section class="card card--back">
    <div class="watermark"></div>
    <div class="brand">
      <span class="brand__dot"></span>
      <span>TERRAVALE GROUNDMAKRZ</span>
      <span>LLC</span>
    </div>
    <h1 class="name"><span class="name__first">DALE</span> <span class="name__last">VORSKIN</span></h1>
    <span class="name-bar"></span>
    <ul class="contacts">
      <li>
        <svg viewBox="0 0 24 24" aria-hidden="true"><path d="M6.6 10.8a15.1 15.1 0 0 0 6.6 6.6l2.2-2.2c.3-.3.7-.4 1-.2 1.1.4 2.3.6 3.6.6.6 0 1 .4 1 1V20c0 .6-.4 1-1 1A17 17 0 0 1 3 4c0-.6.4-1 1-1h3.5c.6 0 1 .4 1 1 0 1.3.2 2.5.6 3.6.1.3 0 .7-.2 1z"/></svg>
        555- 714-9082
      </li>
      <li>
        <svg viewBox="0 0 24 24" aria-hidden="true"><path d="M12 2a10 10 0 1 0 0 20 10 10 0 0 0 0-20zm6.9 6h-3a15.7 15.7 0 0 0-1.3-3.6A8 8 0 0 1 18.9 8zM12 4c.8 1.2 1.5 2.5 1.9 4h-3.8c.4-1.5 1.1-2.8 1.9-4zM4.3 14a8 8 0 0 1 0-4h3.4a16 16 0 0 0 0 4zm.8 2h3a15.7 15.7 0 0 0 1.3 3.6A8 8 0 0 1 5.1 16zm3-8h-3a8 8 0 0 1 4.3-3.6C8.8 5.5 8.4 6.7 8.1 8zM12 20c-.8-1.2-1.5-2.5-1.9-4h3.8c-.4 1.5-1.1 2.8-1.9 4zm2.3-6H9.7a14.7 14.7 0 0 1 0-4h4.6a14.7 14.7 0 0 1 0 4zm.3 5.6c.6-1.1 1-2.3 1.3-3.6h3a8 8 0 0 1-4.3 3.6zm1.7-5.6a16 16 0 0 0 0-4h3.4a8 8 0 0 1 0 4z"/></svg>
        WWW.TRV-GROUNDMAKRZ.COM
      </li>
      <li>
        <svg viewBox="0 0 24 24" aria-hidden="true"><path d="M2 9l10-7 10 7v12H2zm2 2.2V19h16v-7.8l-8 5.3z"/></svg>
        OFFICE@TRV-GROUNDMAKRZ.COM
      </li>
    </ul>
  </section>
</body>
</html>
```